Bookcover: Ways to Turn Into a Bold Pathfinder

I am publishing a super-low-cost innovation book for €4,99 on Quillmere Open Press to help everyone become a great innovator: young ambitious people without college education nor a big budget. Do you want to help me?

Brief:
Design a book cover 1600 x 2560 pixels for QOP.
Main title: Ways to Turn Into a Bold Pathfinder
Sub title: mindset - insights - skills & tools
Author: Joost ter Brakel
Design: captive, and appealing to everyone
Target Group: young ambitious people without college education

For quillmere please format the height/width ratio of 1.6:1

```html
<!DOCTYPE html>
<html lang="en">
<head>
<meta charset="utf-8">
<title>Ways to Turn Into a Bold Pathfinder — Book Cover</title>
<link rel="stylesheet" href="https://fonts.googleapis.com/css2?family=Montserrat:wght@300;400;700;800;900&display=swap">
<style>
  :root {
    --backdrop: #e6e6e6;
    --sky-deep: #14223d;
    --sky-mid: #3b5b86;
    --sky-light: #8fa9c6;
    --glow: #f3e7c2;
    --cloud: #d9dee4;
    --cloud-shade: #7d8793;
    --ink: #0b0b0b;
    --paper: #ffffff;
  }
  * { margin: 0; padding: 0; box-sizing: border-box; }
  html, body {
    width: 1200px;
    height: 678px;
    overflow: hidden;
    background: var(--backdrop);
    font-family: "Montserrat", sans-serif;
  }
  .stage {
    position: relative;
    width: 1200px;
    height: 678px;
    display: flex;
    align-items: center;
    justify-content: center;
  }
  .cover {
    position: relative;
    width: 375px;
    height: 600px;
    overflow: hidden;
    box-shadow: 0 10px 28px rgba(0, 0, 0, 0.22);
  }
  .cover-art {
    position: absolute;
    inset: 0;
    background:
      radial-gradient(ellipse 38% 22% at 52% 48%, var(--glow) 0%, rgba(243, 231, 194, 0) 100%),
      radial-gradient(ellipse 80% 30% at 50% 100%, var(--cloud) 0%, rgba(217, 222, 228, 0.6) 45%, rgba(217, 222, 228, 0) 100%),
      radial-gradient(ellipse 22% 40% at 52% 75%, rgba(235, 238, 242, 0.85) 0%, rgba(235, 238, 242, 0) 100%),
      linear-gradient(180deg, var(--sky-deep) 0%, var(--sky-mid) 35%, var(--sky-light) 62%, var(--cloud-shade) 100%);
  }
  .series-line {
    position: absolute;
    top: 20px;
    left: 0;
    right: 0;
    text-align: center;
    color: var(--paper);
    font-weight: 300;
    font-size: 11.5px;
    letter-spacing: 0.02em;
    text-transform: uppercase;
  }
  .title {
    position: absolute;
    top: 352px;
    left: 0;
    right: 0;
    text-align: center;
    color: var(--ink);
    text-transform: uppercase;
  }
  .title-lead {
    display: block;
    font-weight: 800;
    font-size: 11.5px;
    letter-spacing: 0.1em;
    margin-bottom: 2px;
  }
  .title-main {
    display: block;
    font-weight: 900;
    font-size: 37px;
    line-height: 0.98;
  }
  .author {
    position: absolute;
    bottom: 36px;
    left: 0;
    right: 0;
    text-align: center;
    color: var(--paper);
    font-weight: 800;
    font-size: 14px;
    letter-spacing: 0.06em;
    text-transform: uppercase;
  }
</style>
</head>
<body>
  <main class="stage">
    <section class="cover">
      <div class="cover-art" role="img" aria-label="Photo of a clear light bulb launching upward like a rocket through a blue sky, trailing a glowing plume of white smoke and clouds"></div>
      <p class="series-line">Mindset - Insights - Skills &amp; Tools</p>
      <h1 class="title">
        <span class="title-lead">Ways to Turn Into a</span>
        <span class="title-main">Bold<br>Pathfinder</span>
      </h1>
      <p class="author">Joost ter Brakel</p>
    </section>
  </main>
</body>
</html>
```